New Company Business Card design

Looking for a corporate looking business card utilising my new logo design - the logo i would like embossed as one option and flat as another - simplistic but stylish - less is more - we are an import export business launching into the market - i would like a couple of options as main background - Grey or Black

```html
<!DOCTYPE html>
<html lang="en">
<head>
<meta charset="utf-8">
<title>Meridian Trade Partners – Business Cards</title>
<link href="https://fonts.googleapis.com/css2?family=Cinzel:wght@400;600&family=Arimo:wght@400&display=swap" rel="stylesheet">
<style>
  :root {
    --stage: #1b1b1c;
    --card: #1f1f21;
    --card-edge: #2a2a2d;
    --brand-blue: #1f7fd1;
    --muted-grey: #8a8a8e;
    --text-light: #e6e6e6;
    --rule: #4a4a4e;
  }
  * { box-sizing: border-box; margin: 0; padding: 0; }
  html, body {
    width: 1200px; height: 900px; overflow: hidden;
    background: var(--stage);
  }
  .stage {
    position: relative; width: 1200px; height: 900px;
    display: flex; align-items: center; justify-content: center; gap: 60px;
  }
  .card {
    position: relative; width: 520px; height: 300px;
    background: var(--card);
    border: 1px solid var(--card-edge);
    border-radius: 22px;
    box-shadow: 0 18px 40px rgba(0,0,0,.55);
    overflow: hidden;
  }

  /* Front */
  .card-front {
    display: flex; flex-direction: column; align-items: center; justify-content: center;
  }
  .brand-mark { display: flex; align-items: center; gap: 14px; }
  .brand-dot {
    width: 38px; height: 38px; border-radius: 50%;
    background: var(--brand-blue);
  }
  .brand-name {
    font-family: "Cinzel", serif; font-weight: 600;
    color: var(--brand-blue); font-size: 30px; letter-spacing: 1px;
  }
  .company-name {
    font-family: "Cinzel", serif; font-weight: 600;
    color: var(--brand-blue); font-size: 21px; letter-spacing: 1px;
    margin-top: 18px;
  }
  .company-sub {
    font-family: "Cinzel", serif; font-weight: 400;
    color: var(--muted-grey); font-size: 13px; letter-spacing: 4px;
    padding: 0 30px 3px; border-bottom: 1px solid var(--muted-grey);
  }
  .tagline {
    font-family: "Cinzel", serif; color: var(--muted-grey);
    font-size: 10px; letter-spacing: 3px; margin-top: 5px;
  }
  .website {
    font-family: "Cinzel", serif; color: var(--brand-blue);
    font-size: 12px; letter-spacing: 1.5px; margin-top: 26px;
  }

  /* Back */
  .card-back { padding: 34px 36px; }
  .back-header { border-bottom: 1px solid var(--rule); padding-bottom: 12px; }
  .back-header .company-name { margin-top: 0; font-size: 20px; }
  .back-header .company-sub { display: inline-block; padding: 0 0 3px; font-size: 12px; }
  .back-header .tagline { font-size: 9px; }
  .back-body { display: flex; justify-content: space-between; margin-top: 20px; }
  .person-name {
    font-family: "Cinzel", serif; font-weight: 600; color: var(--brand-blue);
    font-size: 18px; letter-spacing: 1px;
  }
  .person-role {
    font-family: "Arimo", sans-serif; color: var(--text-light);
    font-size: 13px; margin-bottom: 16px;
  }
  .contact-list { list-style: none; font-family: "Arimo", sans-serif; color: var(--text-light); font-size: 13px; }
  .contact-list li { display: flex; align-items: center; gap: 8px; line-height: 20px; }
  .contact-icon { width: 12px; height: 12px; fill: var(--brand-blue); }
  .address {
    font-family: "Arimo", sans-serif; color: var(--text-light); font-style: normal;
    font-size: 13px; text-align: right; line-height: 19px; align-self: flex-start; margin-top: 4px;
  }
</style>
</head>
<body>
<main class="stage">

  <section class="card card-front" aria-label="Business card front">
    <div class="brand-mark">
      <span class="brand-dot"></span>
      <span class="brand-name">MERIDIAN TRADE</span>
    </div>
    <div class="company-name">MERIDIAN TRADE</div>
    <div class="company-sub">PARTNERS</div>
    <div class="tagline">TRUSTED TRADE ACROSS EVERY BORDER</div>
    <div class="website">WWW.MERIDIANTRADE.COM</div>
  </section>

  <section class="card card-back" aria-label="Business card back">
    <header class="back-header">
      <div class="company-name">MERIDIAN TRADE</div>
      <div class="company-sub">PARTNERS</div>
      <div class="tagline">TRUSTED TRADE ACROSS EVERY BORDER</div>
    </header>
    <div class="back-body">
      <div class="person">
        <div class="person-name">DANIEL HART</div>
        <div class="person-role">Managing Director</div>
        <ul class="contact-list">
          <li>
            <svg class="contact-icon" viewBox="0 0 12 12"><path d="M1 4c0-2 2-3 5-3s5 1 5 3l-2 1-1-2H4L3 5zM2 6h8l1 5H1z"/></svg>
            044-555 010 200
          </li>
          <li>
            <svg class="contact-icon" viewBox="0 0 12 12"><rect x="3" y="0.5" width="6" height="11" rx="1.2"/><rect x="4" y="2" width="4" height="6" fill="#1f1f21"/></svg>
            044-555 010 201
          </li>
          <li>
            <svg class="contact-icon" viewBox="0 0 12 12"><rect x="0.5" y="2" width="11" height="8"/><path d="M0.5 2L6 7l5.5-5" fill="none" stroke="#1f1f21" stroke-width="1.2"/></svg>
            info@meridiantrade.com
          </li>
        </ul>
      </div>
      <address class="address">
        12345, Address Goes Here<br>
        Country Name, 123456
      </address>
    </div>
  </section>

</main>
</body>
</html>
```